1 Page for Computer Repair Website

Looking for a 1 page website with a design that compliments the business card and pamphlet that have already been made (attached files). It should look business professional and easy to read. Email and phone number should be somewhere near the top of the website, visible when the page loads. I don't want any forms for people to mess with. No "Contact Us" form or entering in email for newsletter. Customers will just be looking at this site to confirm we are professionals and have our business in order.

Target Market(s)

Home and small business

Industry/Entity Type

Computer Repair

Coding

Coded - Design and coding required

Number of Pages Required

1 page

Font styles to use
Other font styles liked:
• Helvetica variations used in pamphlet and card

Colors
0455a3
cfdeed
85abd2
3276b5
85cae6
ffffff

Requirements
Must have
• Compliment the pamphlet and business card in color choices and font use. Pleasing to the eye and easy to read through categories and text.
Should not have
• Forms. No "enter name and email here" or anything of the sort.

```html
<!DOCTYPE html>
<html lang="en">
<head>
<meta charset="utf-8">
<title>NEXBIT Computer Services</title>
<link href="https://fonts.googleapis.com/css2?family=Roboto:wght@300;400;500;700&display=swap" rel="stylesheet">
<style>
:root{
  --blue:#0455a3;
  --bright:#1e88e5;
  --mid:#3276b5;
  --soft:#85abd2;
  --sky:#85cae6;
  --pale:#cfdeed;
  --navy:#0a2a5c;
  --ink:#333;
  --grey:#777;
  --white:#fff;
}
*{box-sizing:border-box;margin:0;padding:0}
html,body{width:1200px;height:2292px;overflow:hidden}
body{font-family:"Roboto",Helvetica,Arial,sans-serif;color:var(--ink);background:var(--white);position:relative}
.wrap{width:1040px;margin:0 auto;position:relative}
/* header */
.topbar{height:124px}
.brand{position:absolute;left:0;top:32px}
.brand-name{font-size:58px;font-weight:500;color:var(--blue);letter-spacing:1px;line-height:1}
.brand-tag{font-size:15px;color:var(--mid);margin-top:2px;padding-left:4px}
.contact-top{position:absolute;right:0;top:48px;display:flex;gap:40px;font-size:18px;color:var(--blue);font-weight:500}
.contact-top span{display:flex;align-items:center;gap:10px}
/* nav */
.nav{height:48px;background:var(--bright)}
.nav ul{list-style:none;display:flex;height:48px}
.nav li{width:98px;text-align:center;line-height:48px;color:var(--white);font-size:12px;font-weight:500;letter-spacing:.5px}
.nav li.active{background:var(--blue)}
/* hero */
.hero{position:relative;height:588px}
.hero-art{position:absolute;inset:0;background:linear-gradient(120deg,#0b1626 0%,#1f3554 40%,#5c6f86 62%,#1a2a42 85%,#0a1424 100%)}
.hero-text{position:absolute;left:80px;top:212px}
.hero h1{font-size:38px;font-weight:700;color:var(--white);line-height:1.15;text-transform:uppercase}
.hero h1 em{font-style:normal;color:var(--bright)}
.hero p{font-size:14px;color:var(--pale);margin-top:8px}
.btn{display:inline-block;background:var(--bright);color:var(--white);font-size:13px;font-weight:500;padding:14px 28px;letter-spacing:.5px}
.hero .btn{margin-top:42px}
.dots{position:absolute;left:0;right:0;bottom:28px;display:flex;justify-content:center;gap:16px}
.dots i{width:12px;height:12px;border-radius:50%;background:rgba(255,255,255,.45)}
.dots i.on{background:var(--bright)}
/* welcome */
.welcome{height:330px;text-align:center;padding-top:46px}
.welcome h3{font-size:22px;font-weight:400;color:var(--ink)}
.welcome h2{font-size:38px;font-weight:700;color:var(--blue);margin-top:4px}
.welcome p{width:860px;margin:22px auto 0;font-size:14px;line-height:1.75;color:var(--grey)}
.welcome .btn{margin-top:30px}
/* services */
.services{position:relative;height:550px;color:var(--white);text-align:center}
.services-art{position:absolute;inset:0;background:linear-gradient(180deg,#0a2a5c 0%,#06316d 50%,#0a2552 100%)}
.services .wrap{padding-top:60px}
.services h2{font-size:34px;font-weight:700}
.services h2 em{font-style:normal;color:var(--bright)}
.services .intro{width:900px;margin:20px auto 0;font-size:13px;line-height:1.7;color:var(--pale)}
.svc-grid{display:flex;justify-content:space-between;margin-top:50px;padding:0 40px}
.svc{width:210px}
.svc-icon{width:112px;height:112px;border-radius:50%;background:var(--bright);margin:0 auto;display:flex;align-items:center;justify-content:center}
.svc h4{font-size:14px;font-weight:700;margin-top:22px;line-height:1.4;text-transform:uppercase}
.svc p{font-size:12px;color:var(--soft);margin-top:12px;line-height:1.6}
.arrows{display:flex;justify-content:center;gap:12px;margin-top:44px}
.arrows span{width:26px;height:26px;border-radius:50%;border:2px solid var(--white);display:flex;align-items:center;justify-content:center}
/* why / clients */
.split{height:400px;display:flex;justify-content:space-between;padding-top:40px}
.col{width:490px}
.col h2{font-size:32px;font-weight:700;color:var(--ink);text-transform:uppercase}
.col h2 em{font-style:normal;color:var(--bright)}
.why ul{list-style:none;margin-top:26px}
.why li{display:flex;gap:14px;align-items:center;font-size:13px;color:var(--grey);margin-bottom:28px}
.why li i{width:26px;height:26px;border-radius:50%;background:var(--bright);flex:none;display:flex;align-items:center;justify-content:center}
.quote{margin-top:26px;border:1px solid var(--pale);padding:26px 26px 26px 90px;position:relative;font-size:14px;line-height:1.7;color:var(--grey);font-style:italic}
.quote .mark{position:absolute;left:26px;top:26px;font-size:64px;line-height:.8;color:var(--bright);font-style:normal;font-weight:700}
.author{display:flex;gap:16px;align-items:center;margin-top:22px}
.avatar{width:60px;height:60px;border-radius:50%;background:linear-gradient(135deg,var(--soft),var(--mid))}
.author b{display:block;font-size:15px;color:var(--ink)}
.author small{font-size:12px;color:var(--grey)}
/* footer */
.footer{height:210px;background:var(--navy);color:var(--pale)}
.footer .wrap{display:flex;justify-content:space-between;padding-top:36px}
.footer h5{font-size:15px;font-weight:700;color:var(--bright);text-transform:uppercase;margin-bottom:18px}
.fcols{display:flex;gap:60px}
.footer ul{list-style:none;font-size:12px;line-height:1.9}
.footer p{font-size:12px;line-height:1.7}
.contact-col .accent,.hours-col .accent{color:var(--sky)}
.bottom{height:42px;background:#061c40;color:var(--soft);font-size:11px}
.bottom .wrap{display:flex;justify-content:space-between;line-height:42px}
</style>
</head>
<body>
<header class="topbar">
  <div class="wrap">
    <div class="brand"><div class="brand-name">NEXBIT</div><div class="brand-tag">Computer Services</div></div>
    <div class="contact-top">
      <span><svg width="20" height="20" viewBox="0 0 24 24"><path fill="#0455a3" d="M6.6 10.8a15 15 0 0 0 6.6 6.6l2.2-2.2c.3-.3.7-.4 1-.2 1.1.4 2.3.6 3.6.6.6 0 1 .4 1 1V20c0 .6-.4 1-1 1A17 17 0 0 1 3 4c0-.6.4-1 1-1h3.5c.6 0 1 .4 1 1 0 1.3.2 2.5.6 3.6.1.3 0 .7-.2 1z"/></svg>555-201-3480</span>
      <span><svg width="22" height="18" viewBox="0 0 24 18"><rect x="1" y="1" width="22" height="16" rx="2" fill="#0455a3"/><path d="M2 2l10 8 10-8" stroke="#fff" stroke-width="1.6" fill="none"/></svg>help@nexbit.example</span>
    </div>
  </div>
</header>
<nav class="nav">
  <div class="wrap">
    <ul><li class="active">HOME</li><li>ABOUT</li><li>SERVICES</li><li>WHY US</li><li>PRICES</li><li>TESTIMONIALS</li><li>WORKS</li><li>CONTACT</li></ul>
  </div>
</nav>
<section class="hero">
  <div class="hero-art" role="img" aria-label="Close-up photo of a laptop keyboard in dark blue light"></div>
  <div class="hero-text">
    <h1>No pressure to upgrade to <em>products / services</em><br>you don't need or want.</h1>
    <p>Honest advice and repairs for home and small business computers.</p>
    <span class="btn">READ MORE</span>
  </div>
  <div class="dots"><i></i><i></i><i class="on"></i><i></i><i></i></div>
</section>
<section class="welcome">
  <h3>Welcome to</h3>
  <h2>NEXBIT</h2>
  <p>Lorem ipsum dolor sit amet, consectetur adipiscing elit. Donec vitae ex eros. Lorem ipsum dolor sit amet, consectetur adipiscing elit. Vivamus egestas ipsum sed pharetra mattis. Nullam purus felis, bibendum at mollis sed, lobortis blandit felis. Sed quis dolor ultricies, consectetur ipsum nec, lacinia lorem. Mauris sed pharetra urna, at maximus purus. Sed pellentesque hendrerit nibh in tincidunt. Fusce non enim in quam aliquam porta.</p>
  <span class="btn">READ MORE</span>
</section>
<section class="services">
  <div class="services-art" role="img" aria-label="Dark blue photo of computer hardware"></div>
  <div class="wrap">
    <h2>HONEST <em>SERVICES</em></h2>
    <p class="intro">Our certified technicians won't push an upgrade. No pressure to upgrade to products or services you don't need or want. Even the best computers will eventually break down, and if we leave you happy, that's when we hope you'll come back to us.</p>
    <div class="svc-grid">
      <div class="svc"><div class="svc-icon"><svg width="52" height="52" viewBox="0 0 24 24"><circle cx="12" cy="12" r="10" fill="none" stroke="#fff" stroke-width="2"/><path d="M12 5l5 2v4c0 3-2 6-5 7-3-1-5-4-5-7V7z" fill="#fff"/></svg></div><h4>Malware /<br>Virus Removal</h4><p>Lorem Ipsum is simply dummy text of the printing</p></div>
      <div class="svc"><div class="svc-icon"><svg width="52" height="52" viewBox="0 0 24 24"><path d="M4 20l9-9M14 4a4 4 0 0 0 5 5l-2 2-5-5z" stroke="#fff" stroke-width="2.2" fill="none" stroke-linecap="round"/><path d="M20 20l-9-9M4 6l2-2 3 3-2 2z" stroke="#fff" stroke-width="2.2" fill="none" stroke-linecap="round"/></svg></div><h4>PC / Mac / Laptop<br>Hardware Repair</h4><p>Lorem Ipsum is simply dummy text of the printing</p></div>
      <div class="svc"><div class="svc-icon"><svg width="52" height="52" viewBox="0 0 24 24"><path d="M12 4l7 8h-4v8H9v-8H5z" fill="#fff"/></svg></div><h4>Upgrades</h4><p>Lorem Ipsum is simply dummy text of the printing</p></div>
      <div class="svc"><div class="svc-icon"><svg width="52" height="52" viewBox="0 0 24 24"><ellipse cx="12" cy="6" rx="7" ry="2.5" fill="#fff"/><path d="M5 6v12c0 1.4 3 2.5 7 2.5s7-1.1 7-2.5V6" fill="none" stroke="#fff" stroke-width="2"/><path d="M5 12c0 1.4 3 2.5 7 2.5s7-1.1 7-2.5" fill="none" stroke="#fff" stroke-width="2"/></svg></div><h4>Data Migration</h4><p>Lorem Ipsum is simply dummy text of the printing</p></div>
    </div>
    <div class="arrows">
      <span><svg width="10" height="10" viewBox="0 0 10 10"><path d="M7 1L3 5l4 4" stroke="#fff" stroke-width="2" fill="none"/></svg></span>
      <span><svg width="10" height="10" viewBox="0 0 10 10"><path d="M3 1l4 4-4 4" stroke="#fff" stroke-width="2" fill="none"/></svg></span>
    </div>
  </div>
</section>
<section class="wrap split">
  <div class="col why">
    <h2>Why <em>choose us</em></h2>
    <ul>
      <li><i><svg width="12" height="12" viewBox="0 0 12 12"><path d="M2 6l3 3 5-6" stroke="#fff" stroke-width="2" fill="none"/></svg></i>Lorem ipsum dolor sit amet, consectetur adipiscing elit.</li>
      <li><i><svg width="12" height="12" viewBox="0 0 12 12"><path d="M2 6l3 3 5-6" stroke="#fff" stroke-width="2" fill="none"/></svg></i>Consectetur adipiscing elit. Donec vitae ex eros, ipsum dolor.</li>
      <li><i><svg width="12" height="12" viewBox="0 0 12 12"><path d="M2 6l3 3 5-6" stroke="#fff" stroke-width="2" fill="none"/></svg></i>Vivamus egestas ipsum sed pharetra mattis.</li>
      <li><i><svg width="12" height="12" viewBox="0 0 12 12"><path d="M2 6l3 3 5-6" stroke="#fff" stroke-width="2" fill="none"/></svg></i>Pellentesque hendrerit nibh vel vulputate. Nulla nibh arcu.</li>
    </ul>
  </div>
  <div class="col clients">
    <h2>Happy <em>clients</em></h2>
    <div class="quote"><span class="mark">&ldquo;</span>Lorem ipsum dolor sit amet, consectetur adipiscing elit. Cras posuere leo at nisi tincidunt, sed ac dolor facilisis. In et malesuada lacus. Nam lorem sed mauris finibus.</div>
    <div class="author"><div class="avatar" role="img" aria-label="Client portrait photo"></div><div><b>Mark Ellison</b><small>Riverside, CA</small></div></div>
  </div>
</section>
<footer class="footer">
  <div class="wrap">
    <div>
      <h5>Honest services</h5>
      <div class="fcols">
        <ul><li>Malware/Virus Removal</li><li>PC/Mac/Laptop Hardware Repair</li><li>Upgrades</li><li>Data Migration</li></ul>
        <ul><li>Data Restore</li><li>Tune-Up</li><li>In-Home Installation</li><li>Remote Support</li></ul>
      </div>
    </div>
    <div class="hours-col">
      <h5>Service hours</h5>
      <p>Drop-off and in-home visits<br>by appointment only.<br><span class="accent">Saturday, 10–2</span></p>
    </div>
    <div class="contact-col">
      <h5>Contact us</h5>
      <p>NEXBIT COMPUTER SERVICE<br>18 Harbor Lane, Riverside, CA<br><span class="accent">Monday – Friday, 9–5</span><br>Phone: 555-201-3480<br>Email: info@nexbit.example</p>
    </div>
  </div>
</footer>
<div class="bottom"><div class="wrap"><span>&copy;NEXBIT 2015. All Rights Reserved</span><span>TOP</span></div></div>
</body>
</html>
```